Sedona Themed Wedding Invitation & RSVP

*We have added our "Save the Date" for reference. We are not looking for an exact match, but we'd like the invitation and the "Save the Date" to coordinate. Our wedding colors are light pink, light green, cream, and gold. We have also added pictures of bouquets to give you an idea of the color palette and also examples of flowers and greenery to use in the invitation. What we like about the "Save the Date" is that it draws on the wedding colors and brings them in through the colors of the sunset.
*We have also added additional pictures the venue, the Maison Pellerin Lodge, and several maps. We hope that you can use these to get a better feel for our venue and the theme of our wedding. It will be soft and romantic and at the very height of spring.
* We appreciated that many designers incorporated the Lodge at Maison Pellerin, we'd like to see more of that.
*Please note that we included some photos of Sedona for inspiration, please do not feel tied to these, do your own research and find what works best with your design.
*These maps are being included as references, but they are the work of other artists. Please make your own map from scratch and use these as references.
We would like a vertical quad-fold wedding invitation that has a perforated edge RSVP which can be sent as a postcard.
We have attached pictures of a similar style of invitation to serve as an example of the overall style we are looking for. We would like to see the end project be in a similar style of watercolor, but it would be Sedona themed throughout (rather than the forest theme presented in the attached example). We have also attached pictures of Sedona to serve as further inspiration. Below, we have provided an outline organized by panel (four panels on the front and four panels on the back) with descriptions of the more specific details:
-Front four panels:
-Panel 1: "Please join us for the wedding of Tobias and Colette"
-Panel 2: "Come out and celebrate. [INSERT TIME OF WEDDING HERE]
Saturday, May First 2021 at Maison Pellerin Resort"
-Panel 3: Custom map of Sedona. Include Maison Pellerin Resort on the
map (exemplar picture is of an idea for this is also included below)
- Panel 4: RSVP similar to one in the exemplar invitation. For RSVP date
deadline use April 1st, 2021. Address is 2738 E Marlow Ave Phoenix, AZ
85016
-Back four panels:
-Panel 1: Venue: Maison Pellerin Resort. 118 Fennick Way, Sedona, AZ 86351.
Please arrive no earlier than XXX PM when valet services begin. Dinner
and dancing to follow the ceremony
-Panel 2: Hotels: Maison Pellerin Resort 118 Fennick Way, Sedona, AZ 86351
(800) 555-0193; Wrenfield Inn 612 S Halvern Rd, Sedona, AZ 86351
(855) 555-0148.
"Hotel reservations can also be made through the links provided on our
website"
- Panel 3: "We have reserved a block of rooms for our guests. Please
mention the Thorne Pellow Wedding when you call to reserve."
"For additional details, please visit our wedding website and take a walk
down memory lane with us as we prepare to celebrate the rest of our
lives together: [INSERT WEDDING WEBSITE HERE AND
PASSWORD]"
- Panel 4: "Ceremony and celebration will be outdoors. Semi-formal attire
and flat shoes are recommended."
"Additionally, although we love your children, we want our wedding to
be your night off! Please know space is very limited; accordingly, we
encourage a weekend getaway for the grownups."
We'd like to have a succulent and rose at the bottom of the panel (an
exemplar picture is of an idea for this is also included below)
Updates
We have given extensive feedback to designers and would like to give them time to adjust their designs. Additionally, we have incorporated a lot more images into the brief that we hope will help!

```html
<!DOCTYPE html>
<html lang="en">
<head>
<meta charset="utf-8">
<title>Venue &amp; Hotels – Thorne Pellow Wedding</title>
<link rel="stylesheet" href="https://fonts.googleapis.com/css2?family=Pacifico&family=Courgette&family=Dosis:wght@300;400&display=swap">
<style>
  :root {
    --heading-green: #0f6a44;
    --address-brown: #4a3a2e;
    --body-ink: #4c4037;
    --wash-white: #fbfbf6;
    --wash-mint: #dcefd2;
    --wash-green: #c9e6bb;
    --wash-lime: #e4eec6;
    --leaf-green: #7cc58c;
    --leaf-mint: #9fd8c0;
    --succulent: #8fdcae;
    --succulent-deep: #6cc79a;
    --berry-blue: #9fb4cc;
  }
  * { margin: 0; padding: 0; box-sizing: border-box; }
  html, body { width: 1200px; height: 2880px; overflow: hidden; }
  body { background: var(--wash-white); }

  .panel-stack {
    position: relative;
    width: 1200px;
    height: 2880px;
    overflow: hidden;
    background:
      linear-gradient(180deg,
        var(--wash-white) 0px,
        var(--wash-mint) 520px,
        var(--wash-green) 720px,
        #eaf3e1 1100px,
        var(--wash-white) 1440px,
        #f2f3e6 1700px,
        var(--wash-lime) 2050px,
        #e9efcf 2350px,
        var(--wash-white) 2880px);
  }

  .section-title {
    position: absolute;
    font-family: "Pacifico", cursive;
    font-weight: 400;
    font-size: 128px;
    line-height: 1.25;
    color: var(--heading-green);
    white-space: nowrap;
    transform: rotate(-18deg);
    transform-origin: center center;
  }
  .section-title--venue { left: 28px; top: 22px; }
  .section-title--hotels { left: 14px; top: 770px; }

  .address {
    position: absolute;
    left: 0; width: 1200px;
    text-align: center;
    font-family: "Courgette", cursive;
    font-size: 46px;
    line-height: 51px;
    color: var(--address-brown);
  }
  .address--venue { top: 202px; }
  .address--hotel { top: 922px; }

  .note {
    position: absolute;
    left: 0; width: 1200px;
    text-align: center;
    font-family: "Dosis", sans-serif;
    font-weight: 300;
    color: var(--body-ink);
    letter-spacing: -0.04em;
  }
  .note--small { font-size: 27px; line-height: 30px; }
  .note--body { font-size: 38px; line-height: 46px; }
  .note--bold { font-weight: 400; }

  .arrival { top: 456px; }
  .hotel-contacts { top: 1152px; }
  .hotel-links { top: 1286px; }
  .room-block { top: 1646px; }
  .website { top: 1810px; }
  .attire { top: 2276px; }
  .children { top: 2396px; }

  .foliage {
    position: absolute;
    border-radius: 60% 10% 60% 10%;
    opacity: 0.7;
  }
  .bouquet {
    position: absolute;
    left: 258px; top: 2600px;
    width: 682px; height: 230px;
    border-radius: 120px 120px 60px 60px;
    background:
      linear-gradient(90deg,
        var(--berry-blue) 0%,
        var(--succulent) 18%,
        var(--succulent-deep) 38%,
        var(--succulent) 52%,
        var(--succulent-deep) 68%,
        var(--succulent) 84%,
        var(--berry-blue) 100%);
    opacity: 0.75;
  }
</style>
</head>
<body>
<main class="panel-stack">

  <div class="foliage" role="img" aria-label="Watercolour leaf sprig" style="left:1090px;top:0;width:110px;height:160px;background:var(--leaf-mint);"></div>
  <div class="foliage" role="img" aria-label="Watercolour leaf" style="left:505px;top:55px;width:70px;height:45px;background:var(--leaf-mint);opacity:.4;"></div>
  <div class="foliage" role="img" aria-label="Watercolour leafy branch" style="left:880px;top:530px;width:230px;height:180px;background:var(--leaf-green);opacity:.55;"></div>
  <div class="foliage" role="img" aria-label="Watercolour berry sprig" style="left:215px;top:615px;width:90px;height:90px;background:var(--leaf-green);opacity:.35;"></div>
  <div class="foliage" role="img" aria-label="Watercolour berry sprig" style="left:915px;top:780px;width:90px;height:90px;background:var(--leaf-green);opacity:.35;"></div>
  <div class="foliage" role="img" aria-label="Watercolour leafy branch" style="left:120px;top:800px;width:200px;height:140px;background:var(--leaf-green);opacity:.3;"></div>
  <div class="foliage" role="img" aria-label="Watercolour leaves" style="left:0;top:1320px;width:130px;height:120px;background:var(--leaf-green);opacity:.6;"></div>
  <div class="foliage" role="img" aria-label="Watercolour leaf" style="left:635px;top:1360px;width:80px;height:70px;background:var(--leaf-green);opacity:.55;"></div>
  <div class="foliage" role="img" aria-label="Watercolour leaves" style="left:1140px;top:1580px;width:60px;height:170px;background:var(--leaf-green);opacity:.55;"></div>
  <div class="foliage" role="img" aria-label="Watercolour leaves" style="left:930px;top:2110px;width:180px;height:50px;background:var(--leaf-green);opacity:.45;"></div>

  <h1 class="section-title section-title--venue">Venue</h1>
  <p class="address address--venue">Maison Pellerin Resort<br>118 Fennick Way<br>Sedona<br>AZ&nbsp; 86351</p>
  <p class="note note--small arrival">Please arrive no earlier than &nbsp;XXX&nbsp; PM when valet services begin<br>Dinner and dancing to follow the ceremony .</p>

  <h2 class="section-title section-title--hotels">Hotels</h2>
  <p class="address address--hotel">Maison Pellerin Resort<br>118 Fennick Way<br>Sedona<br>AZ&nbsp; 86351</p>
  <p class="note note--small hotel-contacts">(800) 555-0193<br>Wrenfield Inn 612 S Halvern Rd, Sedona, AZ 86351<br>(855) 555-0148</p>
  <p class="note note--small note--bold hotel-links">Hotel reservations can also be made through the links provided on our website .</p>

  <p class="note note--body room-block">We have reserved a block of rooms for our guests. Please<br>mention the Thorne Pellow Wedding when you call to reserve .</p>
  <p class="note note--body website">For additional details, please visit our wedding website and take a walk<br>down memory lane with us as we prepare to celebrate the rest of our<br>lives together .</p>

  <p class="note note--body attire">Ceremony and celebration will be outdoors. Semi-formal attire<br>and flat shoes are recommended.</p>
  <p class="note note--body children">Additionally, although we love your children, we want our wedding to<br>be your night off! Please know space is very limited; accordingly, we<br>encourage a weekend getaway for the grownups .</p>

  <div class="bouquet" role="img" aria-label="Watercolour arrangement of green succulents flanked by blue berry sprigs"></div>

</main>
</body>
</html>
```